Dental Practice Billboard Design

We are a newer dental practice in need of a simple but appealing billboard for our growing dental practice to attract new patients. The practice is owned by husband and wife dentists and is family friendly in a small town in Kentucky. We try to be very friendly and caring to our patients. Would prefer a blue background for the billboard and our tooth logo to be prominent. We are partial to the Patua One font used in the image below but please feel free to tweak it as you deem necessary. The shape of the uppercase D and lowercase g are why we like that font, so fonts with a similarly shaped “D” and “g” would work as well. Please include our phone number (555) 847-1390. Please see our website Harlowbrookdentistry.example for more info on the practice if needed. Thank you! Looking forward to seeing your creation.
Updates

The dimensions will be 12ft x 24ft (3.6576m x 7.3152m). Apologies for not including this in the original prompt. Thank you all for your submissions.

Industry/Entity Type

Dental

Font styles to use
Other font styles liked:
• Patua One

Colors
0054AA
0677BA
7BADD7
CADEEF
E8F1F8
0094D4
00A9DD
6FCCEA
C7EBF8
E9F6FB
00AB8E
00BBA5
67D7C9
C6EFE9
E9F9F6
59FF00
82FF00
B8FF75
E3FFCB
F4FFEA

Requirements
Must have
• Phone number, website, Logo, Practice name “Harlow Brook Dentistry”
Should not have
• A tagline or slogan

```html
<!DOCTYPE html>
<html lang="en">
<head>
<meta charset="utf-8">
<title>Harlow Brook Dentistry – Billboard Set</title>
<link rel="stylesheet" href="https://fonts.googleapis.com/css2?family=Patua+One&display=swap">
<style>
  :root {
    --brand-blue: #2a5ba8;
    --ink-blue: #2453a0;
    --brand-green: #2aa845;
    --cream: #efe9d8;
    --photo-warm: #b0674f;
    --photo-light: #d9d4cc;
    --white: #ffffff;
    --page: #ffffff;
  }
  * { margin: 0; padding: 0; box-sizing: border-box; }
  html, body { width: 1200px; height: 1200px; overflow: hidden; background: var(--page); }
  body { position: relative; font-family: "Patua One", Georgia, serif; }

  .billboard { position: absolute; width: 334px; height: 167px; overflow: hidden; }

  /* Cream billboard with team photo */
  .billboard--photo { left: 162px; top: 169px; display: flex; background: var(--cream); }
  .billboard__info { width: 152px; display: flex; flex-direction: column; align-items: center; justify-content: center; color: var(--ink-blue); padding-top: 4px; }
  .lockup { display: flex; align-items: center; gap: 6px; }
  .lockup__dot { border-radius: 50%; flex: none; background: var(--brand-green); }
  .billboard--photo .lockup__dot { width: 14px; height: 14px; }
  .billboard--photo .lockup__name { font-size: 14.5px; line-height: 1.05; }
  .billboard--photo .phone { font-size: 16px; margin-top: 13px; display: flex; align-items: center; gap: 4px; }
  .billboard--photo .website { font-size: 6px; margin-top: 20px; }
  .billboard__photo { flex: 1; background: linear-gradient(100deg, var(--photo-light) 0%, #cfc7bd 45%, var(--photo-warm) 100%); }

  .phone-icon { width: 0.95em; height: 0.95em; flex: none; }

  /* Round badge */
  .badge { position: absolute; left: 770px; top: 488px; width: 168px; height: 168px; }
  .badge text { font-family: "Patua One", Georgia, serif; fill: var(--white); }

  /* Blue billboard */
  .billboard--blue { left: 162px; top: 920px; background: var(--brand-blue); color: var(--white); display: flex; align-items: center; padding-left: 30px; gap: 26px; }
  .billboard--blue .lockup__dot { width: 52px; height: 52px; }
  .billboard__text { display: flex; flex-direction: column; align-items: center; }
  .billboard--blue .name-main { font-size: 30px; line-height: 1; }
  .billboard--blue .name-sub { font-size: 22px; line-height: 1.15; }
  .billboard--blue .phone { font-size: 22px; display: flex; align-items: center; gap: 5px; margin-top: 3px; }
  .billboard--blue .website { font-size: 8.5px; margin-top: 12px; letter-spacing: 0.3px; }
</style>
</head>
<body>

  <section class="billboard billboard--photo">
    <div class="billboard__info">
      <div class="lockup">
        <span class="lockup__dot"></span>
        <span class="lockup__name">Harlow Brook<br>Dentistry</span>
      </div>
      <div class="phone">
        <svg class="phone-icon" viewBox="0 0 24 24" aria-hidden="true"><path fill="currentColor" d="M6.6 10.8a15 15 0 0 0 6.6 6.6l2.2-2.2a1 1 0 0 1 1-.25 11.4 11.4 0 0 0 3.6.57 1 1 0 0 1 1 1V20a1 1 0 0 1-1 1A17 17 0 0 1 3 4a1 1 0 0 1 1-1h3.5a1 1 0 0 1 1 1c0 1.25.2 2.45.57 3.57a1 1 0 0 1-.25 1z"/></svg>
        (555) 847-1390
      </div>
      <div class="website">www.Harlowbrookdentistry.example</div>
    </div>
    <div class="billboard__photo" role="img" aria-label="Photo of the two dentists in white coats smiling in front of a brick wall"></div>
  </section>

  <svg class="badge" viewBox="0 0 172 172" role="img" aria-label="Round sign: Harlow Brook Dentistry, (555) 847-1390">
    <defs>
      <path id="arc-top" d="M 19 97.8 A 68 68 0 1 1 153 97.8"/>
      <path id="arc-bottom" d="M 25.4 121 A 70 70 0 0 0 154.9 98.2"/>
    </defs>
    <circle cx="86" cy="86" r="86" fill="var(--brand-blue)"/>
    <text font-size="17.5"><textPath href="#arc-top" startOffset="50%" text-anchor="middle">Harlow Brook Dentistry</textPath></text>
    <text font-size="17"><textPath href="#arc-bottom" startOffset="24">(555) 847-1390</textPath></text>
    <g transform="translate(21 104) rotate(-30)">
      <path fill="var(--white)" transform="scale(0.55)" d="M6.6 10.8a15 15 0 0 0 6.6 6.6l2.2-2.2a1 1 0 0 1 1-.25 11.4 11.4 0 0 0 3.6.57 1 1 0 0 1 1 1V20a1 1 0 0 1-1 1A17 17 0 0 1 3 4a1 1 0 0 1 1-1h3.5a1 1 0 0 1 1 1c0 1.25.2 2.45.57 3.57a1 1 0 0 1-.25 1z"/>
    </g>
    <circle cx="86" cy="86" r="18" fill="var(--brand-green)"/>
  </svg>

  <section class="billboard billboard--blue">
    <span class="lockup__dot"></span>
    <div class="billboard__text">
      <div class="name-main">Harlow Brook</div>
      <div class="name-sub">Dentistry</div>
      <div class="phone">
        <svg class="phone-icon" viewBox="0 0 24 24" aria-hidden="true"><path fill="currentColor" d="M6.6 10.8a15 15 0 0 0 6.6 6.6l2.2-2.2a1 1 0 0 1 1-.25 11.4 11.4 0 0 0 3.6.57 1 1 0 0 1 1 1V20a1 1 0 0 1-1 1A17 17 0 0 1 3 4a1 1 0 0 1 1-1h3.5a1 1 0 0 1 1 1c0 1.25.2 2.45.57 3.57a1 1 0 0 1-.25 1z"/></svg>
        (555) 847-1390
      </div>
      <div class="website">www.Harlowbrookdentistry.example</div>
    </div>
  </section>

</body>
</html>
```